WordPress Design for both website and landing page for an expert

I need a clean and stylish design for my new website. I work as an expert (see attached file WHY HOW WHAT), my product is expert opinion (reports) for company evaluations You can use all of the attached pictures colored or black / white. The person is me, you can add other pictures, if you want. The design should be clean and stylish, so you could use white, black, gray, silver and / or one additional color. I have added an idea about my website, see attached file CONCEPT WEBSITE If you have any more information, please do not hesitate to contact us 'Hesitate to ask me ...

```html
<!DOCTYPE html>
<html lang="de">
<head>
<meta charset="utf-8">
<title>Tobias Kellner – Expert for Company Valuations</title>
<link href="https://fonts.googleapis.com/css2?family=Open+Sans:wght@300;400;600;700&display=swap" rel="stylesheet">
<style>
:root{
  --black:#0b0b0c;
  --blue:#1d4f9e;
  --blue-light:#3a7bd5;
  --grey-bg:#eeeff1;
  --grey-mid:#9aa0a6;
  --grey-dark:#5a5f66;
  --text:#333639;
  --line:#d9dbde;
  --white:#ffffff;
  --diagram-a:#e8f0e4;
  --diagram-b:#e3eef2;
}
*{margin:0;padding:0;box-sizing:border-box}
html,body{width:1200px;height:3944px;overflow:hidden}
body{font-family:"Open Sans",Arial,sans-serif;color:var(--text);background:var(--white);position:relative}
.abs{position:absolute}

/* nav */
.site-nav{left:0;top:0;width:1200px;height:108px;background:var(--black)}
.brand{left:40px;top:22px;display:flex;flex-direction:column;align-items:center;color:var(--white)}
.brand-mark{width:28px;height:28px;border:2px solid var(--white)}
.brand-name{margin-top:8px;font-size:13px;letter-spacing:4px;font-weight:400}
.nav-links{right:40px;top:44px;display:flex;gap:46px;font-size:12px;font-weight:600;letter-spacing:.5px;color:var(--white)}
.nav-links .active{color:var(--blue-light)}

/* hero */
.hero{left:0;top:108px;width:1200px;height:572px;background:linear-gradient(180deg,#5b8fd6 0%,#2f68b8 35%,#1b3a66 62%,#0d1b33 100%)}
.hero-title{left:0;top:180px;width:1200px;text-align:center;color:var(--white);font-weight:700;font-size:30px;letter-spacing:1px}
.hero-sub{left:0;top:226px;width:1200px;text-align:center;color:var(--white);font-weight:300;font-size:27px;line-height:38px}

/* reasons */
.reasons{left:0;top:680px;width:1200px;height:480px;background:var(--grey-bg)}
.reasons-photo{left:600px;top:680px;width:600px;height:480px;background:linear-gradient(120deg,#e9e9ea,#cfd0d2 55%,#b9bbbf)}
.reasons-title{left:112px;top:748px;font-size:30px;font-weight:300;line-height:40px;color:var(--text);letter-spacing:.5px}
.rule{height:2px;width:36px;background:var(--blue)}
.reason{left:112px;width:490px;height:48px;border:1px solid var(--line);background:var(--white);font-size:16px;padding:13px 14px;display:flex;align-items:baseline;gap:10px}
.reason small{font-size:10px;color:var(--grey-mid)}

/* why choose */
.section-title{width:1200px;left:0;text-align:center;font-size:26px;font-weight:300;letter-spacing:1px}
.card{top:1288px;width:304px;height:304px;border:1px solid var(--line);background:var(--white);text-align:center;padding-top:44px}
.card-icon{width:80px;height:80px;border-radius:50%;background:#6c7075;margin:0 auto;display:flex;align-items:center;justify-content:center}
.card h3{font-size:15px;font-weight:400;margin-top:40px;letter-spacing:1px}
.card p{font-size:11px;color:var(--grey-dark);line-height:19px;margin:14px 30px 0}

/* promise */
.promise{left:0;top:1640px;width:1200px;height:400px;background:var(--grey-bg)}
.promise-brand{left:0;top:1700px;width:1200px;display:flex;flex-direction:column;align-items:center}
.promise-mark{width:70px;height:70px;border:4px solid #8b9096}
.promise-name{margin-top:18px;font-size:30px;letter-spacing:7px;color:#6a6f75;font-weight:400}
.promise-title{left:0;top:1880px;width:1200px;text-align:center;font-size:22px;font-weight:600;letter-spacing:1px}
.promise-text{left:0;top:1926px;width:1200px;text-align:center;font-size:14px;line-height:22px;color:var(--text)}

/* what how why */
.diagram{left:150px;top:2120px;width:400px;height:380px;border-radius:8px;background:linear-gradient(135deg,var(--diagram-a),var(--diagram-b))}
.pillar{left:590px;width:520px}
.pillar h2{font-size:28px;font-weight:400;letter-spacing:1px}
.pillar p{font-size:11px;color:var(--grey-dark);line-height:19px;margin-top:14px}

/* about */
.about-photo{left:140px;top:2620px;width:332px;height:560px;background:linear-gradient(180deg,#bfbfbf,#7d7d7d 55%,#3e3e3e)}
.about-card{left:520px;top:2660px;width:580px;height:380px;background:var(--white);box-shadow:0 4px 22px rgba(0,0,0,.18);padding:38px 40px}
.about-card h2{font-size:26px;font-weight:400;letter-spacing:1px}
.about-card h4{font-size:13px;font-weight:600;margin-top:18px}
.about-card ul{list-style:none;font-size:10px;color:var(--grey-dark);line-height:17px;margin-top:6px}
.partners{left:860px;top:2860px;width:200px}
.partners h4{font-size:13px;font-weight:600}
.badge{width:110px;height:52px;border-radius:6px;background:linear-gradient(180deg,#f2f3f5,#d4d7db);border:1px solid var(--line);margin-top:14px}

/* contact */
.contact{left:0;top:3280px;width:1200px;height:460px;background:linear-gradient(180deg,#f6f6f7,#e6e7e9)}
.contact-text{left:0;top:3386px;width:1200px;text-align:center;font-size:11px;color:var(--grey-dark);line-height:18px}
.field{height:32px;border:1px solid var(--line);background:var(--white);font-size:11px;padding:8px 10px;color:var(--grey-dark)}
.submit{left:526px;top:3648px;width:142px;height:42px;background:var(--blue);color:var(--white);font-size:12px;font-weight:600;letter-spacing:1px;text-align:center;line-height:42px}

/* footer */
.site-footer{left:0;top:3740px;width:1200px;height:204px;background:var(--black)}
.footer-brand{left:0;top:3772px;width:1200px;display:flex;flex-direction:column;align-items:center;color:var(--white)}
.footer-brand .brand-name{font-size:20px;letter-spacing:6px;margin-top:12px}
.footer-brand .brand-mark{width:40px;height:40px}
.copyright{left:0;top:3896px;width:1200px;text-align:center;font-size:11px;color:#c9cbce}
</style>
</head>
<body>

<header class="abs site-nav">
  <div class="abs brand"><span class="brand-mark"></span><span class="brand-name">TOBIAS KELLNER</span></div>
  <nav class="abs nav-links">
    <span class="active">HOME</span><span>WHAT I DO</span><span>WHY I DO IT &amp; HOW I DO IT</span><span>ABOUT ME</span><span>CONTACT</span>
  </nav>
</header>

<section class="abs hero" role="img" aria-label="Photo of a city riverside skyline with a TV tower at dusk"></section>
<h1 class="abs hero-title">EXPERT FOR COMPANY VALUATIONS</h1>
<p class="abs hero-sub">Sie benötigen ein Gutachten zur Ermittlung des<br>Wertes Ihres Unternehmens</p>

<section class="abs reasons"></section>
<div class="abs reasons-photo" role="img" aria-label="Photo of the expert in a white shirt leaning on a balcony railing"></div>
<h2 class="abs reasons-title">WHAT DO YOU NEED OR CAN<br>USE A REPORT FOR</h2>
<div class="abs rule" style="left:112px;top:840px"></div>
<div class="abs reason" style="top:872px">Reason 1 <small>Bewertung beim Kauf oder Verkauf</small></div>
<div class="abs reason" style="top:944px">Reason 2 <small>Nachfolge und Erbfall</small></div>
<div class="abs reason" style="top:1016px">Reason 3 <small>Gesellschafterwechsel oder Scheidung</small></div>

<h2 class="abs section-title" style="top:1216px">WHY CHOOSE US</h2>
<div class="abs rule" style="left:582px;top:1260px"></div>
<div class="abs card" style="left:112px">
  <div class="card-icon"><svg width="40" height="40" viewBox="0 0 40 40"><path d="M4 20 L36 6 L26 34 L19 23 Z M19 23 L36 6" fill="none" stroke="#fff" stroke-width="2"/></svg></div>
  <h3>SCHNELL</h3>
  <p>Sie bekommen Ihr Gutachten zügig und verlässlich, in der Regel innerhalb von nur zwei Wochen nach Eingang aller Unterlagen.</p>
</div>
<div class="abs card" style="left:448px">
  <div class="card-icon"><svg width="40" height="40" viewBox="0 0 40 40"><circle cx="20" cy="20" r="14" fill="none" stroke="#fff" stroke-width="2"/><path d="M13 20 L18 25 L27 15" fill="none" stroke="#fff" stroke-width="2.5"/></svg></div>
  <h3>ZERTIFIZIERT</h3>
  <p>Sie erhalten ein geprüftes und belastbares Gutachten von einem zertifizierten Sachverständigen nach anerkannten Standards.</p>
</div>
<div class="abs card" style="left:784px">
  <div class="card-icon"><svg width="40" height="40" viewBox="0 0 40 40"><rect x="10" y="6" width="20" height="28" fill="none" stroke="#fff" stroke-width="2"/><path d="M14 14h12M14 20h12M14 26h8" stroke="#fff" stroke-width="2"/></svg></div>
  <h3>VERSTÄNDLICH</h3>
  <p>Ihr Gutachten wird klar gegliedert und nachvollziehbar geschrieben, damit jede Aussage für Sie gut verständlich bleibt.</p>
</div>

<section class="abs promise"></section>
<div class="abs promise-brand"><span class="promise-mark"></span><span class="promise-name">TOBIAS KELLNER</span></div>
<h2 class="abs promise-title">MEIN QUALITÄTSVERSPRECHEN:</h2>
<p class="abs promise-text">Sollte der zugesagte Termin für die Erstellung des Gutachtens überschritten<br>werden, erhalten Sie das Gutachten absolut kostenfrei!<br>(Ich verzichte auf mein Honorar)</p>

<div class="abs diagram" role="img" aria-label="Illustration of three overlapping circles labelled what, how and why"></div>

<div class="abs pillar" style="top:2110px">
  <h2>WHAT I DO</h2>
  <p>Ich erstelle unabhängige Gutachten zur Bewertung von Unternehmen, klar begründet und für Käufer, Verkäufer und Gerichte belastbar dokumentiert.</p>
</div>
<div class="abs pillar" style="top:2236px">
  <h2>HOW I DO</h2>
  <p>Jedes Gutachten beginnt mit einem Gespräch. Danach analysiere ich alle Zahlen sorgfältig und erkläre Ihnen jeden Schritt der Bewertung offen.</p>
</div>
<div class="abs pillar" style="top:2362px">
  <h2>WHY I DO</h2>
  <p>Unternehmen sind meine Leidenschaft. Jede Firma ist einzigartig, und ich möchte ihren wahren Wert sichtbar und verständlich machen.</p>
</div>

<div class="abs about-photo" role="img" aria-label="Black and white photo of the expert in a suit"></div>
<article class="abs about-card">
  <h2>ABOUT TOBIAS M. KELLNER</h2>
  <div class="rule" style="margin-top:10px"></div>
  <h4>Professional Experience</h4>
  <ul>
    <li>20 years as managing director of a mid-sized company</li>
    <li>15 years as certified business valuer in private practice</li>
    <li>Member of several valuation expert panels</li>
  </ul>
  <h4>Educations</h4>
  <ul>
    <li>Diploma in business administration</li>
    <li>Certified valuation expert (university)</li>
    <li>Master of business valuation</li>
    <li>Trained mediator for company succession</li>
    <li>Seminar series on corporate finance</li>
  </ul>
</article>
<div class="abs partners">
  <h4>Our Partners</h4>
  <div class="badge"></div>
  <div class="badge"></div>
</div>

<section class="abs contact"></section>
<h2 class="abs section-title" style="top:3322px">CONTACT US</h2>
<div class="abs rule" style="left:582px;top:3364px"></div>
<p class="abs contact-text">Haben Sie Fragen zu meinen Gutachten oder wünschen Sie ein unverbindliches Angebot?<br>Schreiben Sie mir einfach eine kurze Nachricht, ich melde mich gerne zeitnah bei Ihnen.</p>
<div class="abs field" style="left:300px;top:3480px;width:292px">First Name</div>
<div class="abs field" style="left:608px;top:3480px;width:292px">Last Name</div>
<div class="abs field" style="left:300px;top:3522px;width:292px">Phone</div>
<div class="abs field" style="left:608px;top:3522px;width:292px">Email</div>
<div class="abs field" style="left:300px;top:3564px;width:600px;height:60px">Message</div>
<div class="abs submit">SUBMIT</div>

<footer class="abs site-footer"></footer>
<div class="abs footer-brand"><span class="brand-mark"></span><span class="brand-name">TOBIAS KELLNER</span></div>
<p class="abs copyright">© Copyright 2016 · Tobias Kellner All Rights Reserved</p>

</body>
</html>
```